MyName is TapLedger .... Killer of Business Cards!!! WANT a KickAss Design Landing Page :)

How 'TapLedger' works:
- with a unique name for each country, like a personalise car plate number
- our platform links through a 'Quick Text' keyword short code
- TapLedger platform will respond with downloaded ready full contact business file link
- this is designed to be downloaded in just '3 clicks' into your Contacts Folder
- any changes,,updates, images, online profiles can be made in real time updates
- TapLedger provides a backend login to manage individual account and is ready
Enterprise model for larger staff companies
- platform is international ready and have launched
Australia, in September 2019.

Yes, your whole business card and online profile in '3' simple clicks. No '20-30 mins' of typing the business card contacts details into mobile phones.
** Fact: 88% of business cards are lost of thrown out within 7 days.
(https://www.plumfinchstats.com/business-card-statistics.html) **

NZ ClipStream
https://vidhost.example/q7Rt2LmP9xZ

**current websites are www.tapledge.co.nz www.taplink.com.au www.tapledgerau.com www.tapledgerus.com **

Target Market(s)

Anybody who uses a business card, from trades person, real estate agents, consultants, bankers (in NZ/AU with have plumbers, financial advisors, real estate agents, mortgage brokers, sports agents, Telcos etc etc)

Industry/Entity Type

Business Software

Coding

Coded - Design and coding required

Number of Pages Required

4 page

Font styles to use
Other font styles liked:
• libre franklin black

Requirements
Must have
• TapLedger a simple 'in delivery' and smart 'in innovation' solution so our message is Simple, Clear and Inquisitive. We would like a converting landing page because we are selling Nimble Cloud Suite at low-entry cost and no-contract. IWe want to direct clients to a name reservation platform to a virtual business card that uses our Nimble Core Engine. We will require some code at the back to link the name reservation and sign up source code(javascript). This web/landing page fresh page is required because we have recently changed our marketing strategy to be purely digital marketing in Chatterbook and Snapgrid Ads from now on. We would like this to be exciting graphically to grab attention, inquisitive enough to check your name availability and follow through with call to action with the right colours and graphics images. We plan to test the right pitch offering until we get the markets feedback on the best offering/re-design and then push harder with more CB and SG Ads. ( **we plan to continue multiple regular campaigns as the business has now change our strategy due to covid-19 and we will focus mainly on direct to consumers**)

Also:
2 buttons: Signup and a Check availability little form to allow a java script to be added/HTML5/CB advertising/Super Inviting to check 'YOUR UNIQUE NAME' is available. Then clicking the to reserve the name to purchase our Quick Text/Eco-Friendly/Relevant to todays tech and Low Cost service. We will be offering Promo codes for each campaign.
No Apps. Works with SMS, any smartphone, country specific, enterprise ready, and CONTACTLESS ....
Nice to have
• Personal feeling. Unique choice of 'your name' as this is your business and social profile in one. Strong independent images and confident to share with anybody their profile by just sharing their name.
Should not have
• Open currently....

```html
<!DOCTYPE html>
<html lang="en">
<head>
<meta charset="utf-8">
<title>TapLedger – Your business card in 3 clicks</title>
<link rel="stylesheet" href="https://fonts.googleapis.com/css2?family=Libre+Franklin:wght@500;600;800;900&family=Raleway:ital,wght@0,300;0,400;0,500;0,600;1,400&display=swap">
<style>
:root{
  --teal:#137a87;
  --teal-dark:#0f6a75;
  --navy:#1f3b6e;
  --footer:#22417a;
  --ink:#222;
  --muted:#777;
  --rule:#e3e3e3;
  --gold:#a88b4c;
  --light:#f2f2f2;
}
*{box-sizing:border-box;margin:0;padding:0}
html,body{width:1200px;height:3422px;overflow:hidden}
body{font-family:"Raleway",sans-serif;color:var(--ink);background:#fff;position:relative}
a{color:inherit;text-decoration:none}
.btn{display:inline-flex;align-items:center;justify-content:center;background:var(--teal);color:#fff;font-family:"Libre Franklin",sans-serif;font-weight:600;font-size:16px;letter-spacing:.2px}

/* header */
.site-header{height:101px;position:relative}
.brand{position:absolute;left:110px;top:18px;display:flex;align-items:center;gap:10px}
.brand-mark{width:34px;height:34px;border:3px solid var(--teal);border-radius:50%}
.brand-name{font-family:"Libre Franklin",sans-serif;font-weight:800;font-size:24px;color:var(--navy);letter-spacing:.5px}
.main-nav{position:absolute;left:354px;top:0;height:101px;display:flex;align-items:center;gap:37px;font-size:15px;color:#444}
.main-nav .btn{position:absolute;left:597px;top:28px;width:137px;height:52px;font-size:15px}

/* hero */
.hero{height:558px;position:relative;background:linear-gradient(100deg,#3a3f45 0%,#6a6c6b 35%,#9c9b97 60%,#d7d5d0 100%)}
.hero-panel{position:absolute;left:182px;top:133px;width:836px;height:275px;background:rgba(40,40,40,.55);text-align:center;color:#fff}
.hero-title{font-family:"Libre Franklin",sans-serif;font-weight:900;font-size:78px;letter-spacing:1px;margin-top:22px;line-height:1}
.hero-sub{font-size:16px;line-height:32px;margin:14px auto 0;width:620px}
.hero-panel .btn{width:212px;height:50px;margin-top:18px}
.slide-arrow{position:absolute;width:20px;height:30px}

/* benefits */
.benefits{height:869px;position:relative}
.section-title{font-family:"Libre Franklin",sans-serif;font-weight:800;font-size:44px;text-align:center;color:#1e1e1e;letter-spacing:.3px}
.benefits .section-title{padding-top:94px}
.benefit-grid{position:absolute;left:110px;top:178px;width:980px;display:grid;grid-template-columns:repeat(4,231px);grid-auto-rows:243px;column-gap:18px;row-gap:19px}
.benefit-card{border:1px solid var(--rule);box-shadow:0 1px 4px rgba(0,0,0,.08);padding:12px 11px}
.benefit-icon{width:50px;height:52px;stroke:var(--teal);fill:none;stroke-width:2}
.benefit-name{font-family:"Libre Franklin",sans-serif;font-weight:500;font-size:16px;margin:15px 0 10px;letter-spacing:.4px}
.benefit-text{font-size:13px;line-height:20.5px;color:var(--muted);text-align:justify}
.benefits .btn{position:absolute;left:508px;top:716px;width:184px;height:51px;font-size:17px}

/* video */
.video-band{height:469px;position:relative;background:linear-gradient(90deg,#9a7e42 0%,#ab8f52 50%,#a88b4c 100%)}
.play{position:absolute;left:556px;top:190px;width:88px;height:88px}

/* plans */
.plans{height:641px;position:relative;background:linear-gradient(180deg,#f3f3f3,#e9e9e9)}
.plans .section-title{padding-top:96px}
.plan-card{position:absolute;top:178px;width:316px;height:359px;color:#fff;text-align:center;padding-top:128px}
.plan-card.personal{left:262px;background:var(--teal)}
.plan-card.business{left:622px;background:var(--navy)}
.plan-name{font-size:22px;font-weight:500;letter-spacing:.6px}
.plan-text{font-size:15px;line-height:26px;margin:14px auto 0;width:260px}
.plan-card .btn{width:154px;height:50px;margin-top:13px;font-family:"Raleway",sans-serif;font-weight:500;font-size:15px}
.personal .btn{background:var(--navy)}
.business .btn{background:var(--teal)}

/* testimonials */
.testimonials{height:403px;position:relative;background:#f4f4f4;text-align:center}
.testimonials .section-title{padding-top:46px}
.quote{width:880px;margin:26px auto 0;font-style:italic;font-size:15.5px;line-height:32px;color:#444;position:relative}
.quote-mark{color:#8fc6c9;font-family:"Libre Franklin",sans-serif;font-weight:900;font-size:30px;position:absolute;line-height:1}
.client-name{font-size:26px;color:var(--navy);margin-top:32px}
.client-role{font-size:14px;color:#999;margin-top:10px}

/* footer */
.site-footer{height:381px;position:relative;background:var(--footer);color:#fff}
.col{position:absolute;top:76px}
.col h4{font-family:"Libre Franklin",sans-serif;font-weight:500;font-size:16px;letter-spacing:.4px;margin-bottom:24px}
.quick li{list-style:none;font-size:15.5px;height:37px}
.contact-row{display:flex;gap:18px;font-size:15.5px;line-height:25px;margin-bottom:18px}
.contact-row svg{flex:none;width:16px;height:16px;margin-top:5px;stroke:#fff;fill:none;stroke-width:1.6}
.social li{list-style:none;display:flex;align-items:center;gap:10px;height:39px;font-size:15.5px}
.social .dot{width:30px;height:30px;border:2px solid #fff;border-radius:50%}
.news-input{width:247px;height:44px;background:#fff;color:#888;font-size:13px;padding:0 8px;display:flex;align-items:center;margin-top:-3px}
.news-btn{width:137px;height:42px;margin-top:17px;font-size:16px}
.footer-rule{position:absolute;left:110px;top:299px;width:978px;border-top:1px solid rgba(255,255,255,.5)}
.pay-cards{position:absolute;left:114px;top:325px;display:flex;gap:4px}
.pay-cards span{width:36px;height:24px;border-radius:3px}
.copyright{position:absolute;left:0;width:1200px;top:326px;text-align:center;font-size:15px}
</style>
</head>
<body>

<header class="site-header">
  <a class="brand" href="#"><span class="brand-mark"></span><span class="brand-name">TAPLEDGER</span></a>
  <nav class="main-nav">
    <a href="#">HOME</a><a href="#">PARTNERS</a><a href="#">BENEFITS</a><a href="#">PLANS</a><a href="#">TESTIMONIALS</a><a href="#">LOG IN</a>
    <a class="btn" href="#">SIGN UP</a>
  </nav>
</header>

<section class="hero" role="img" aria-label="Photo of a hand holding a smartphone showing a text message chat, on a desk with a notebook, pen, coffee cup and keyboard">
  <svg class="slide-arrow" style="left:82px;top:366px" viewBox="0 0 20 30"><path d="M15 3 L4 15 L15 27" stroke="#fff" stroke-width="2" fill="none"/></svg>
  <svg class="slide-arrow" style="left:1098px;top:366px" viewBox="0 0 20 30"><path d="M5 3 L16 15 L5 27" stroke="#fff" stroke-width="2" fill="none"/></svg>
  <div class="hero-panel">
    <h1 class="hero-title">TAPLEDGER</h1>
    <p class="hero-sub">TapLedger is the intelligent, relevant and easy way for your new customers or friends to receive ALL of your contact card information</p>
    <a class="btn" href="#">CHECK AVAILABILITY</a>
  </div>
</section>

<section class="benefits">
  <h2 class="section-title">SIMPLE BENEFITS ARE</h2>
  <div class="benefit-grid">
    <article class="benefit-card">
      <svg class="benefit-icon" viewBox="0 0 50 52"><rect x="6" y="4" width="22" height="42" rx="3"/><circle cx="34" cy="24" r="9"/><path d="M30 24h1M34 24h1M38 24h1"/></svg>
      <h3 class="benefit-name">LOGICAL</h3>
      <p class="benefit-text">Everybody has a mobile phone and every phone can txt/sms.</p>
    </article>
    <article class="benefit-card">
      <svg class="benefit-icon" viewBox="0 0 50 52"><circle cx="25" cy="10" r="5"/><path d="M17 26c0-5 4-8 8-8s8 3 8 8z"/><path d="M4 38l10-6h14l-10 6h16l10-8M4 46h30l14-10"/></svg>
      <h3 class="benefit-name">PROFESSIONAL</h3>
      <p class="benefit-text">Your customers / potential customers will be impressed with your innovation.</p>
    </article>
    <article class="benefit-card">
      <svg class="benefit-icon" viewBox="0 0 50 52"><path d="M6 10h14l4 4h20v32H6z"/><rect x="10" y="24" width="16" height="18"/><path d="M30 26h10M30 32h10M30 38h10"/></svg>
      <h3 class="benefit-name">DATA SAFE</h3>
      <p class="benefit-text">All data is held on a secure Cirrovault infrastructure in Sydney, which puts strong safeguards in place to protect your customer privacy.</p>
    </article>
    <article class="benefit-card">
      <svg class="benefit-icon" viewBox="0 0 50 52"><rect x="4" y="6" width="36" height="24" rx="2"/><path d="M4 14h36"/><path d="M34 24l10 4v8c0 6-5 10-10 12-5-2-10-6-10-12v-8z"/><path d="M29 35l4 4 6-7"/></svg>
      <h3 class="benefit-name">SECURE PAYMENT</h3>
      <p class="benefit-text">Back by the global Tillquay payment gateway. Tillquay a certified as a PCI Level One Service Provider. This is the most stringent level of certification available gateway industry.</p>
    </article>
    <article class="benefit-card">
      <svg class="benefit-icon" viewBox="0 0 50 52"><circle cx="22" cy="28" r="16"/><path d="M10 20c6 2 8 8 4 14M28 14c-2 6 4 10 10 8"/><path d="M34 12c4-6 10-6 12-4-2 6-8 8-12 4z"/></svg>
      <h3 class="benefit-name">ENVIRONMENT</h3>
      <p class="benefit-text">No use of business cards, you no longer need to have cards printed, thus reducing your carbon foot print.</p>
    </article>
    <article class="benefit-card">
      <svg class="benefit-icon" viewBox="0 0 50 52"><rect x="3" y="12" width="44" height="30" rx="3"/><path d="M3 20h44"/><path d="M9 32h12M9 36h8"/><rect x="30" y="30" width="10" height="7"/></svg>
      <h3 class="benefit-name">EASE</h3>
      <p class="benefit-text">So simple to share and retrieve your TapLedger.</p>
    </article>
    <article class="benefit-card">
      <svg class="benefit-icon" viewBox="0 0 50 52"><circle cx="16" cy="30" r="11"/><circle cx="16" cy="30" r="5"/><path d="M26 24l12-10v20z"/><path d="M38 14h6v20h-6"/><path d="M10 42l-2 8h16l-2-8"/></svg>
      <h3 class="benefit-name">SALES</h3>
      <p class="benefit-text">May increase your sales by word of mouth, added to your advertising and ability to share TapLedger anywhere, anytime.</p>
    </article>
    <article class="benefit-card">
      <svg class="benefit-icon" viewBox="0 0 50 52"><path d="M6 14l4-8 4 4 4-6 4 6 4-4 4 8z"/><circle cx="18" cy="32" r="14"/><path d="M22 25h-6a3 3 0 0 0 0 6h4a3 3 0 0 1 0 6h-6M18 22v20"/><rect x="32" y="24" width="14" height="22"/><path d="M35 30h8M35 35h8M35 40h8"/></svg>
      <h3 class="benefit-name">COST</h3>
      <p class="benefit-text">The service is less per year than the average sales persons cost in business cards</p>
    </article>
  </div>
  <a class="btn" href="#">VIEW ALL</a>
</section>

<section class="video-band" role="img" aria-label="Video cover: illustration of a payment card rising from a smartphone among floating app icons, with the title TapLedger Virtual Card">
  <svg class="play" viewBox="0 0 88 88"><circle cx="44" cy="44" r="40" fill="#fff" stroke="#1f2a44" stroke-width="6"/><path d="M36 30l22 14-22 14z" fill="#111"/></svg>
</section>

<section class="plans">
  <h2 class="section-title">PLANS FOR EVERYONE</h2>
  <div class="plan-card personal">
    <h3 class="plan-name">PERSONAL PLAN</h3>
    <p class="plan-text">Provides for one keyword and one personal TapLedger. For $4.99 + gst / month</p>
    <a class="btn" href="#">GET STARETD</a>
  </div>
  <div class="plan-card business">
    <h3 class="plan-name">BUSINESS PLAN</h3>
    <p class="plan-text">Provides for one personal and business keyword. For $6.99 + gst / month</p>
    <a class="btn" href="#">GET STARETD</a>
  </div>
</section>

<section class="testimonials">
  <h2 class="section-title">OUR CLIENTS LOVE US!</h2>
  <svg class="slide-arrow" style="left:82px;top:188px" viewBox="0 0 20 30"><path d="M15 3 L4 15 L15 27" stroke="#333" stroke-width="2" fill="none"/></svg>
  <svg class="slide-arrow" style="left:1098px;top:188px" viewBox="0 0 20 30"><path d="M5 3 L16 15 L5 27" stroke="#333" stroke-width="2" fill="none"/></svg>
  <blockquote class="quote">
    <span class="quote-mark" style="left:-8px;top:-6px">&ldquo;</span>This service gained me 10 listings for me over the past year! For me is the best and most powerful tool available in the Real Estate industry. I often get caught out in social occasions, bars, restaurants, expos, the beach, everywhere without a business card, but with TapLedger I can instantly have all my details sent directly to my potential customers phone and most powerfully a web link directly to my profile page with all my listings. I would highly recommend it to anyone.<span class="quote-mark" style="position:relative;top:10px">&rdquo;</span>
  </blockquote>
  <p class="client-name">Mara Kellaway</p>
  <p class="client-role">Licensee Salesperson, Harbourline Realty Limited</p>
</section>

<footer class="site-footer">
  <div class="col" style="left:128px">
    <h4>QUICKLINKS</h4>
    <ul class="quick"><li>Partners</li><li>Benefits</li><li>Plans</li><li>Testimonials</li><li>Log in</li></ul>
  </div>
  <div class="col" style="left:311px">
    <h4>CONTACT US</h4>
    <div class="contact-row"><svg viewBox="0 0 16 16"><path d="M3 1l3 3-2 2c1 3 3 5 6 6l2-2 3 3-2 2C7 15 1 9 1 3z"/></svg><span>70418326519</span></div>
    <div class="contact-row"><svg viewBox="0 0 16 16"><path d="M8 15s5-5 5-9a5 5 0 0 0-10 0c0 4 5 9 5 9z"/><circle cx="8" cy="6" r="1.6"/></svg><span>27 Tidewater Parade,<br>Seabrook, Gold Coast QLD 4299</span></div>
    <div class="contact-row"><svg viewBox="0 0 16 16"><rect x="1" y="3" width="14" height="10"/><path d="M1 3l7 6 7-6"/></svg><span>support@tapledger.com.au</span></div>
  </div>
  <div class="col" style="left:624px">
    <h4 style="margin-left:5px">CONNECT WITH US</h4>
    <ul class="social"><li><span class="dot"></span>Chatterbook</li><li><span class="dot"></span>Snapgrid</li><li><span class="dot"></span>Chirpline</li><li><span class="dot"></span>Linkfold</li></ul>
  </div>
  <div class="col" style="left:840px">
    <h4>NEWSLETTER</h4>
    <div class="news-input">Enter Name</div>
    <a class="btn news-btn" href="#">SUBSCRIBE</a>
  </div>
  <div class="footer-rule"></div>
  <div class="pay-cards" aria-label="Accepted payment cards">
    <span style="background:#e8a13a"></span><span style="background:#f4f4f4"></span><span style="background:#5aa6d6"></span><span style="background:#e6e6e6"></span>
  </div>
  <p class="copyright">© 2020 All Rights Reserved</p>
</footer>

</body>
</html>
```